Sleek wordpress site for Bramblecrest finishing works

We are a commercial job shop that serves B2B, govt & LEO and retail clients.We need a wordpress site with 6 individual pages: homepage, coating, laser engraving, laser cutting, part marking, and contact us. I have attached an outline of the desired flow and sub headings for each page. I would like to incorporate the colors of the logo through out the site to be clean and sleek enough to appeal to B2B commercial clients yet be inviting enough for retail clients.

I would like to have easy picture functionality so photographs on each page can be updated easily.

Target Market(s)

B2B industrial & Govt and Military part marking, laser engraving and coating: machine shops, aerospace companies, tool manufactures. Retail: personalized gifts, Job Shop

Coding

Coded - Design and coding required

Font styles to use
Sans Serif
Other font styles liked:
• Open to suggestion

Colors
0255a3
3176b5
eaf1f7
cfdeed
ffffff

Requirements
Must have
• Clean easy to navigate flow, separate pages as indicated on attached outline, high class feel. Great picture functionality, professional and inviting feel,
• **update: needs to be optimized for mobile, should have a gallery function. Gallery can be an additional page or embedded
Nice to have
• Social media connectivity links,
Should not have
• crappy plugins that make back-end management difficult, no blog

```html
<!DOCTYPE html>
<html lang="en">
<head>
<meta charset="utf-8">
<title>Bramblecrest Finishing Works</title>
<link href="https://fonts.googleapis.com/css2?family=Lato:wght@400;700;900&family=Roboto:wght@400;500;700&display=swap" rel="stylesheet">
<style>
:root{
  --blue:#0255a3;
  --blue-mid:#3176b5;
  --blue-pale:#eaf1f7;
  --blue-soft:#cfdeed;
  --white:#ffffff;
  --ink:#1c1c1c;
  --text:#555;
  --ghost:#e9e9e9;
  --footer:#0d0d0d;
}
*{margin:0;padding:0;box-sizing:border-box}
html,body{width:1200px;height:3000px;overflow:hidden}
body{position:relative;background:var(--white);font-family:"Roboto",Arial,sans-serif;color:var(--ink)}
.abs{position:absolute}
/* header */
.site-header{position:absolute;left:0;top:0;width:1200px;height:118px;background:var(--white);border-top:3px solid var(--blue);z-index:3}
.nav a{position:absolute;top:50px;font:500 14px "Roboto",sans-serif;color:#222;text-decoration:none;letter-spacing:.3px}
.nav a.active{color:var(--blue)}
.brand-disc{position:absolute;left:490px;top:-40px;width:220px;height:220px;border-radius:50%;background:var(--white);z-index:4;text-align:center}
.brand-mark{margin:70px auto 0;width:76px;height:76px;border-radius:50%;border:5px solid var(--blue);font:900 26px/66px "Lato",sans-serif;color:var(--blue)}
.brand-name{font:700 15px "Lato",sans-serif;color:var(--blue);margin-top:6px;letter-spacing:.2px}
.brand-tag{font:400 9px "Lato",sans-serif;color:#444;margin-top:2px}
/* hero */
.hero-photo{position:absolute;left:0;top:118px;width:1200px;height:640px;background:radial-gradient(ellipse at 36% 58%,#fff6d8 0,#f1a64a 7%,#8a5a3a 20%,#3d3634 45%,#1c1c1e 80%)}
.hero-title{position:absolute;left:568px;top:268px;font:700 44px "Roboto",sans-serif;color:var(--white);letter-spacing:.5px}
.hero-sub{position:absolute;left:570px;top:342px;width:540px;font:500 21px/32px "Roboto",sans-serif;color:var(--white)}
.btn{position:absolute;display:block;background:var(--blue);color:var(--white);border-radius:26px;font:700 16px "Roboto",sans-serif;text-align:center;text-decoration:none}
.arrow-dot{position:absolute;width:34px;height:34px;border-radius:50%;background:rgba(0,0,0,.55)}
/* services */
.ghost{position:absolute;font:900 72px "Lato",sans-serif;color:var(--ghost);white-space:nowrap}
.section-title{position:absolute;font:900 36px "Lato",sans-serif;color:var(--ink)}
.section-lead{position:absolute;left:0;width:1200px;text-align:center;font:400 13px "Roboto",sans-serif;color:var(--text)}
.service{position:absolute;top:955px;width:320px;text-align:center}
.service h3{margin-top:28px;font:700 19px "Roboto",sans-serif;color:var(--ink)}
.service p{margin-top:14px;font:400 12.5px/24px "Roboto",sans-serif;color:var(--text)}
.plain-arrow{position:absolute;font:400 30px "Roboto",sans-serif;color:#555}
/* gallery strip */
.tile{position:absolute;top:1306px;width:300px;height:276px}
.tile span{position:absolute;left:0;width:300px;text-align:center;font:700 22px "Roboto",sans-serif}
/* about */
.about-title{position:absolute;left:98px;top:1668px;font:900 34px "Lato",sans-serif;color:var(--ink)}
.about-text{position:absolute;left:98px;width:540px;font:400 13px/24px "Roboto",sans-serif;color:var(--text);text-align:justify}
.video-frame{position:absolute;left:732px;top:1682px;width:402px;height:268px;border:3px solid var(--blue)}
.video-still{position:absolute;left:696px;top:1714px;width:406px;height:272px;border:4px solid var(--white);box-shadow:0 2px 8px rgba(0,0,0,.2);background:linear-gradient(135deg,#1a1a1f 0,#5b1016 35%,#c8262b 60%,#e7e7e7 100%)}
.rule{position:absolute;left:98px;top:2084px;width:1002px;height:1px;background:#ddd}
.sub-title{position:absolute;font:900 22px "Lato",sans-serif;color:var(--ink)}
.ghost-sm{position:absolute;font:900 50px "Lato",sans-serif;color:var(--ghost);white-space:nowrap}
.small-arrow{position:absolute;font:400 20px "Roboto",sans-serif;color:#666}
.client{position:absolute;width:148px;height:76px;border:1px solid #ddd;background:var(--white);font:700 15px/74px "Lato",sans-serif;color:#333;text-align:center}
.quote-box{position:absolute;left:628px;top:2220px;width:472px;height:130px;background:#e6e6e6;border:2px solid #cfcfcf;padding:22px 26px 0 30px;font:italic 400 12px/22px "Roboto",sans-serif;color:#555}
.quote-box b{font:700 26px "Lato",sans-serif;color:#999;position:absolute;left:14px;top:10px}
.author{position:absolute;left:628px;top:2372px;width:472px;text-align:center;font:500 19px "Roboto",sans-serif;color:#333}
.author em{font-size:12px;font-weight:400}
/* footer */
.footer{position:absolute;left:0;top:2590px;width:1200px;height:410px;background:var(--footer)}
.f-head{position:absolute;top:2606px;font:700 19px "Lato",sans-serif;color:var(--white)}
.f-head i{font-style:normal;font-weight:400;color:var(--blue-mid)}
.f-list{position:absolute;left:98px;top:2662px;list-style:none}
.f-list li{font:400 12.5px/26px "Roboto",sans-serif;color:var(--white)}
.f-list li::before{content:"›";margin-right:10px;font-weight:700}
.f-text{position:absolute;font:400 12.5px/24px "Roboto",sans-serif;color:var(--white)}
.field{position:absolute;height:42px;border:1px solid #bbb;font:400 12px/40px "Roboto",sans-serif;color:var(--white);padding-left:12px}
.submit{position:absolute;left:872px;top:2782px;width:228px;height:42px;background:var(--blue);color:var(--white);font:700 16px/42px "Roboto",sans-serif;text-align:center}
.f-rule{position:absolute;left:98px;top:2896px;width:1002px;height:1px;background:#555}
.social{position:absolute;top:2934px;width:28px;height:28px;border-radius:50%;border:2px solid var(--white)}
</style>
</head>
<body>

<header class="site-header">
  <nav class="nav">
    <a class="active" style="left:106px">HOME</a>
    <a style="left:198px">COATING</a>
    <a style="left:310px">LASER ENGRAVING</a>
    <a style="left:718px">LASER CUTTING</a>
    <a style="left:878px">PART MARKING</a>
    <a style="left:1032px">CONTACT</a>
  </nav>
</header>
<div class="brand-disc">
  <div class="brand-mark">BFW</div>
  <div class="brand-name">BRAMBLECREST FINISHING</div>
  <div class="brand-tag">coating · marking · engraving</div>
</div>

<section class="hero">
  <div class="hero-photo" role="img" aria-label="Laser cutter head throwing bright orange sparks over a steel sheet"></div>
  <div class="arrow-dot" style="left:40px;top:368px"></div>
  <svg class="abs" style="left:51px;top:378px" width="12" height="14"><path d="M9 1 3 7l6 6" stroke="#fff" stroke-width="2.5" fill="none"/></svg>
  <div class="arrow-dot" style="left:1126px;top:368px"></div>
  <svg class="abs" style="left:1138px;top:378px" width="12" height="14"><path d="M3 1l6 6-6 6" stroke="#fff" stroke-width="2.5" fill="none"/></svg>
  <h1 class="hero-title">BRAMBLECREST FINISHING</h1>
  <p class="hero-sub">Duraglaze is a spray on ceramic based finish that can be applied to metals, plastics, polymers and wood.</p>
  <a class="btn" style="left:570px;top:432px;width:196px;height:52px;line-height:52px">READ MORE ➔</a>
  <svg class="abs" style="left:0;top:620px" width="1200" height="140" viewBox="0 0 1200 140">
    <path d="M0 20 Q600 200 1200 10 L1200 140 L0 140Z" fill="var(--blue)"/>
    <path d="M0 40 Q600 210 1200 34 L1200 140 L0 140Z" fill="var(--white)"/>
  </svg>
</section>

<section class="services">
  <div class="ghost" style="left:346px;top:810px">OUR SERVICES</div>
  <h2 class="section-title" style="left:478px;top:832px">OUR SERVICES</h2>
  <p class="section-lead" style="top:897px">We offer the wide range of services to help our customer's create whatever they needs</p>
  <div class="plain-arrow" style="left:40px;top:1068px">‹</div>
  <div class="plain-arrow" style="left:1144px;top:1068px">›</div>

  <svg class="abs" style="left:186px;top:955px" width="116" height="128" viewBox="0 0 116 128">
    <path d="M58 4a54 54 0 0 1 26 101L58 124 32 105A54 54 0 0 1 58 4Z" fill="var(--blue)"/>
    <circle cx="58" cy="58" r="44" fill="none" stroke="#fff" stroke-width="3"/>
    <rect x="40" y="40" width="36" height="36" fill="none" stroke="#fff" stroke-width="3"/>
    <path d="M48 66l22-22" stroke="#fff" stroke-width="3"/>
  </svg>
  <svg class="abs" style="left:542px;top:955px" width="116" height="128" viewBox="0 0 116 128">
    <path d="M58 4a54 54 0 0 1 26 101L58 124 32 105A54 54 0 0 1 58 4Z" fill="var(--blue)"/>
    <circle cx="58" cy="58" r="44" fill="none" stroke="#fff" stroke-width="3"/>
    <path d="M42 40l26 30M74 40 48 70" stroke="#fff" stroke-width="3"/>
    <circle cx="44" cy="74" r="6" fill="none" stroke="#fff" stroke-width="3"/>
    <circle cx="72" cy="74" r="6" fill="none" stroke="#fff" stroke-width="3"/>
  </svg>
  <svg class="abs" style="left:896px;top:955px" width="116" height="128" viewBox="0 0 116 128">
    <path d="M58 4a54 54 0 0 1 26 101L58 124 32 105A54 54 0 0 1 58 4Z" fill="var(--blue)"/>
    <circle cx="58" cy="58" r="44" fill="none" stroke="#fff" stroke-width="3"/>
    <path d="M58 80 44 56 58 34 72 56Z M58 34v-6 M40 40h36" stroke="#fff" stroke-width="3" fill="none"/>
  </svg>

  <div class="service" style="left:84px"><h3 style="margin-top:150px">LASER ENGRAVING</h3><p>Capabilities Statement: With our selection<br>of CO2 and fiber lasers there are very few materials<br>and substrates that we cannot mark</p></div>
  <div class="service" style="left:440px"><h3 style="margin-top:150px">LASER CUTTING</h3><p>BFW can custom cut virtually any shape or design in<br>a variety of substrates or materials. Custom cut items<br>can be fabricated from wood, foam</p></div>
  <div class="service" style="left:794px"><h3 style="margin-top:150px">PART MARKING</h3><p>Nemo enim ipsam voluptatem quia voluptas<br>sit aspernatur aut odit aut fugit, sed quia consequu<br>tur magni dolores eos qui ratione volupta</p></div>
</section>

<section class="gallery-strip">
  <div class="tile" style="left:0;background:linear-gradient(160deg,#c9ccd2,#3c4f8a 55%,#c7621f)" role="img" aria-label="Laser engraving machine working on a metal part"><span style="top:216px;color:rgba(255,255,255,.35)">LASER ENGRAVING</span></div>
  <div class="tile" style="left:300px;background:linear-gradient(180deg,#6c7078,#2c2f34 60%,#111)" role="img" aria-label="Laser cutting nozzle close up with sparks"><span style="top:120px;color:#fff">LASER CUTTING</span></div>
  <div class="tile" style="left:600px;background:radial-gradient(circle at 50% 55%,#f0c7f0,#8a4a7a 18%,#3a3438 55%,#1e1e20)" role="img" aria-label="Plasma cutter marking a steel plate"><span style="top:216px;color:rgba(255,255,255,.35)">PART MARKING</span></div>
  <div class="tile" style="left:900px;background:linear-gradient(150deg,#2c2c2c,#553a30 50%,#b25b40)" role="img" aria-label="Gloved hands spraying a coating onto a part"><span style="top:216px;color:rgba(255,255,255,.35)">COATINGS</span></div>
</section>

<section class="about">
  <div class="ghost" style="left:752px;top:1606px">ABOUT US</div>
  <h2 class="about-title">ABOUT BRAMBLECREST FINISHING</h2>
  <p class="about-text" style="top:1742px">Nemo enim ipsam voluptatem quia voluptas sit aspernatur aut odit aut fugit, sed quia conse-quuntur magni dolores eos qui ratione voluptatem sequi nesciunt.</p>
  <p class="about-text" style="top:1808px">Neque porro quisquam est, qui dolorem ipsum quia dolor sit amet, consectetur, adipisci velit, sed quia non numquam eius modi tempora incidunt ut labore et dolore magnam aliquam quaerat voluptatem. Ut enim ad minima veniam, quis nostrum exercitationem ullam corporis suscipit laboriosam, nisi ut aliquid commodi consequatur...</p>
  <a class="btn" style="left:98px;top:1938px;width:160px;height:48px;line-height:48px;font-size:15px;font-weight:500">READ MORE ➔</a>
  <div class="video-frame"></div>
  <div class="video-still" role="img" aria-label="Video still of a laser cutting head over a lettered metal sheet"></div>
  <svg class="abs" style="left:872px;top:1834px" width="44" height="34"><rect width="44" height="34" rx="8" fill="#222"/><path d="M17 9v16l13-8Z" fill="#fff"/></svg>
</section>

<div class="rule"></div>

<section class="clients">
  <div class="ghost-sm" style="left:0;top:2140px">OUR CLIENTS</div>
  <h2 class="sub-title" style="left:98px;top:2158px">OUR CLIENTS</h2>
  <div class="small-arrow" style="left:546px;top:2158px">‹</div>
  <div class="small-arrow" style="left:572px;top:2158px">›</div>
  <div class="client" style="left:98px;top:2218px">Harlow Sodas</div>
  <div class="client" style="left:264px;top:2218px">Veridane</div>
  <div class="client" style="left:432px;top:2218px">Corvel Cola</div>
  <div class="client" style="left:98px;top:2316px">Ashgrove Labs</div>
  <div class="client" style="left:264px;top:2316px">Kestrion</div>
  <div class="client" style="left:432px;top:2316px">Ostler &amp; Co</div>
</section>

<section class="testimonials">
  <div class="ghost-sm" style="left:830px;top:2140px">TESTIMONIALS</div>
  <h2 class="sub-title" style="left:626px;top:2158px">TESTIMONIALS</h2>
  <div class="small-arrow" style="left:1068px;top:2158px">‹</div>
  <div class="small-arrow" style="left:1092px;top:2158px">›</div>
  <div class="quote-box"><b>“</b>At vero eos et accusamus et iusto odio dignissimos ducimus qui blanditiis pre sentium voluptatum deleniti atque corrupti quos dolores et quas molestias excepturi sint occaecati cupiditate non provident,</div>
  <svg class="abs" style="left:660px;top:2348px" width="24" height="16"><path d="M0 0h24L6 16Z" fill="#e6e6e6" stroke="#cfcfcf" stroke-width="2"/></svg>
  <div class="author">Marla Quint, <em>Creative Manager, USA</em></div>
</section>

<svg class="abs" style="left:0;top:2470px" width="1200" height="130" viewBox="0 0 1200 130">
  <path d="M0 90 Q600 -40 1200 90 L1200 130 L0 130Z" fill="var(--blue)"/>
  <path d="M0 112 Q600 -14 1200 112 L1200 130 L0 130Z" fill="var(--footer)"/>
</svg>

<footer class="footer"></footer>
<h3 class="f-head" style="left:96px">QUICK <i>LINKS</i></h3>
<ul class="f-list">
  <li>Home</li><li>Coating</li><li>Laser Engraving</li><li>Laser Cutting</li><li>Part Marking</li><li>Gallery</li><li>Contact Us</li>
</ul>
<h3 class="f-head" style="left:324px">CONTACT <i>US</i></h3>
<svg class="abs" style="left:324px;top:2672px" width="14" height="18"><path d="M7 17C2 10 1 8 1 6a6 6 0 0 1 12 0c0 2-1 4-6 11Z" fill="#fff"/><circle cx="7" cy="6" r="2.2" fill="#0d0d0d"/></svg>
<p class="f-text" style="left:354px;top:2664px">418 W Juniper Ave #7, Tempe,<br>AZ 85281</p>
<svg class="abs" style="left:324px;top:2730px" width="16" height="16"><path d="M3 1l3 0 2 4-2 2c1 2 2 3 4 4l2-2 4 2v3c0 1-1 2-2 2C7 16 0 9 1 3c0-1 1-2 2-2Z" fill="#fff"/></svg>
<p class="f-text" style="left:354px;top:2726px">(+1) 555 014 2290</p>
<svg class="abs" style="left:324px;top:2782px" width="16" height="16"><circle cx="8" cy="8" r="6.5" fill="none" stroke="#fff" stroke-width="2"/><path d="M8 4v4l3 2" stroke="#fff" stroke-width="1.6" fill="none"/></svg>
<p class="f-text" style="left:356px;top:2778px;white-space:pre">Mon - Weds:    9am-5:30pm
Thu - Fri:        9am-7pm
Sat - Sun:        11am-3pm</p>
<h3 class="f-head" style="left:632px">GET A <i>QUOTE</i></h3>
<p class="f-text" style="left:632px;top:2656px;width:470px">Bramblecrest Finishing offer the wide range of services to help our customer's create whatever they needs.</p>
<div class="field" style="left:632px;top:2726px;width:228px">Name</div>
<div class="field" style="left:872px;top:2726px;width:228px">Email</div>
<div class="field" style="left:632px;top:2782px;width:228px">Phone No</div>
<div class="submit">SUBMIT</div>
<div class="f-rule"></div>
<p class="f-text" style="left:98px;top:2936px">Copyrights © 2018 Bramblecrest Finishing.  All Rights Reserved    |    Privacy Policy.</p>
<h3 class="f-head" style="left:830px;top:2936px">FOLLOW <i>US</i></h3>
<div class="social" style="left:966px"></div>
<div class="social" style="left:1002px"></div>
<div class="social" style="left:1038px"></div>
<div class="social" style="left:1074px"></div>

</body>
</html>
```